IT Product Event Invitations

We are requesting the design of two invitations for a series of technological events that will be held between the company Tidewell Labs and its partner in the Dominican Republic, Corvantel.
Both events represent the launch of the Tidewell Labs brand in the Dominican Republic.
The first event is an elegant dinner aimed at the banking sector of the Dominican Republic to showcase the "Ledgerline Banking Suite" software.
Event information:
- Descriptive text for the invitation: Corvantel y Tidewell Labs le invitan a descubrir cómo reducir costos, aumentar la automatización y mejorar la satisfacción de los clientes a través de una solución única para enfrentar los desafíos de la banca.
- Date: 25 de Septiembre
- Time: 7PM
- Location: El Pimiento, Av. Julián Marcano 318
In the invitation, consider using the colors of the Tidewell Labs and Corvantel brands if possible. You can find the logos in the webpage
The second event is a wine tasting to present "Harborview Operations Hub" aimed at various industries.
Event information:
- Descriptive text for the invitation: Corvantel y Tidewell Labs le invitan a conocer una solución que le permitirá a toda su empresa brindar una experiencia de servicio a otro nivel.
- Date: 26 de Septiembre
- Time: 7PM
In the invitation, consider using the colors of the Tidewell Labs and Corvantel brands if possible. You can find the logos in the web page.
Both invitations must have a button for participant registration and that when you click on the image, it will direct you to a form.
Form for Ledgerline Banking Suite: https://signup.corvantel-events.example/ledgerline-dinner
Form for Harborview Operations Hub: https://signup.corvantel-events.example/harborview-tasting
Target Market(s)
Enterprise Customers
Industry/Entity Type
Technology
Look and feel
Each slider illustrates characteristics of the customer's brand and the style your logo design should communicate.

```html
<!DOCTYPE html>
<html lang="es">
<head>
<meta charset="utf-8">
<title>Invitaciones Corvantel y Tidewell Labs</title>
<link href="https://fonts.googleapis.com/css2?family=Cinzel:wght@700;800&family=Bebas+Neue&family=Poppins:wght@400;500;600;700&family=Mr+Dafoe&display=swap" rel="stylesheet">
<style>
  :root {
    --stage: #d6d6d6;
    --paper: #fbfaf8;
    --red: #c8282a;
    --red-deep: #b81f22;
    --orange: #f15a22;
    --amber: #f7941d;
    --ink: #141414;
    --green: #62b54a;
    --gold: #ecdcb8;
  }
  * { margin: 0; padding: 0; box-sizing: border-box; }
  html, body { width: 1200px; height: 803px; overflow: hidden; }
  body { background: var(--stage); position: relative; font-family: "Poppins", sans-serif; color: var(--ink); }

  .invitation {
    position: absolute; top: 69px; width: 513px; height: 663px;
    background: var(--paper); overflow: hidden;
  }
  .invitation--dinner { left: 62px; }
  .invitation--tasting { left: 617px; }

  .side-band { position: absolute; top: 0; width: 38px; height: 100%;
    background: linear-gradient(180deg, var(--amber) 0%, var(--orange) 22%, #e8321e 45%, var(--orange) 68%, #f9a257 88%, var(--orange) 100%); }
  .side-band--left { left: 0; }
  .side-band--right { right: 0; }

  .marble { position: absolute; left: 38px; right: 38px; height: 120px; }
  .marble--top { top: 0; background: radial-gradient(ellipse at 70% 0%, rgba(236,220,184,.55), rgba(236,220,184,0) 70%); }
  .marble--bottom { bottom: 0; background: radial-gradient(ellipse at 40% 100%, rgba(236,220,184,.6), rgba(236,220,184,0) 70%); }

  .content { position: absolute; left: 38px; right: 38px; top: 0; bottom: 0; text-align: center; }

  .greeting { position: absolute; top: 44px; left: 0; right: 0;
    font-family: "Mr Dafoe", cursive; font-size: 38px; line-height: 1; color: var(--ink); z-index: 2; }

  .event-title { position: absolute; left: 0; right: 0;
    font-family: "Cinzel", serif; font-weight: 800; letter-spacing: -1px; white-space: nowrap;
    background: linear-gradient(180deg, var(--red-deep) 0%, var(--red) 45%, var(--orange) 100%);
    -webkit-background-clip: text; background-clip: text; color: transparent; }
  .event-title--dinner { font-size: 86px; line-height: .74; top: 76px; }
  .event-title--tasting { font-size: 76px; line-height: .82; top: 76px; }

  .lead { position: absolute; top: 207px; left: 0; right: 0;
    font-size: 10px; letter-spacing: 3.4px; font-weight: 500; }
  .product { position: absolute; top: 219px; left: 0; right: 0;
    font-size: 13px; font-weight: 700; letter-spacing: -.1px; }

  .date { position: absolute; top: 252px; left: 0; right: 0; }
  .date-day { font-family: "Cinzel", serif; font-weight: 800; font-size: 92px; line-height: 1;
    color: var(--red); display: inline-block; position: relative; }
  .date-de { position: absolute; right: -30px; top: -6px;
    font-family: "Mr Dafoe", cursive; font-size: 38px; color: var(--ink); font-weight: 400; }
  .date-month { display: block; font-family: "Bebas Neue", sans-serif; font-size: 44px; line-height: 1; margin-top: -4px; }

  .details { position: absolute; top: 393px; left: 0; right: 0; height: 66px; }
  .details-divider { position: absolute; left: 247px; top: 0; width: 2px; height: 66px; background: var(--green); }
  .time { position: absolute; left: 66px; top: 12px; width: 94px; }
  .time-label { font-size: 17px; letter-spacing: 4px; font-weight: 500; }
  .time-value { margin-top: 2px; background: linear-gradient(90deg, var(--red) 0%, var(--orange) 100%);
    color: #fff; font-weight: 600; font-size: 27px; line-height: 29px; border-radius: 2px; }
  .place { position: absolute; left: 249px; right: 0; top: 3px; font-size: 12.5px; line-height: 15px; }
  .place svg { display: block; margin: 0 auto 4px; }

  .blurb { position: absolute; left: 24px; right: 24px; font-size: 9.6px; line-height: 11.5px; }
  .invitation--dinner .blurb { top: 488px; }
  .invitation--tasting .blurb { top: 494px; left: 22px; right: 22px; }

  .partners { position: absolute; top: 533px; left: 0; right: 0; display: flex; justify-content: center; align-items: center; gap: 24px; }
  .partner { display: flex; align-items: center; gap: 6px; font-weight: 700; font-size: 19px; color: var(--ink); }
  .partner-dot { width: 22px; height: 22px; border-radius: 50%; background: var(--orange); }

  .register { position: absolute; top: 592px; left: 50%; transform: translateX(-50%); height: 14px;
    display: inline-flex; align-items: center; border: 1px solid var(--orange); border-radius: 8px; overflow: hidden;
    text-decoration: none; color: var(--ink); white-space: nowrap; }
  .register-label { background: linear-gradient(90deg, var(--red), var(--orange)); color: #fff; white-space: nowrap;
    font-weight: 700; font-size: 8.5px; height: 100%; padding: 0 9px; line-height: 13px; border-radius: 8px; }
  .register-url { font-size: 6px; padding: 0 8px 0 7px; white-space: nowrap; }
</style>
</head>
<body>

<article class="invitation invitation--dinner">
  <div class="side-band side-band--left"></div>
  <div class="side-band side-band--right"></div>
  <div class="marble marble--top" role="img" aria-label="Textura de mármol dorado suave"></div>
  <div class="marble marble--bottom" role="img" aria-label="Textura de mármol dorado suave"></div>
  <div class="content">
    <p class="greeting">Estás invitado a la</p>
    <h1 class="event-title event-title--dinner">CENA<br>ANUAL</h1>
    <p class="lead">PARA PRESENTAR EL SOFTWARE</p>
    <p class="product">LEDGERLINE BANKING SUITE</p>
    <div class="date"><span class="date-day">25<span class="date-de">de</span></span><span class="date-month">SEPTIEMBRE</span></div>
    <div class="details">
      <div class="time"><p class="time-label">TIME</p><p class="time-value">7 PM</p></div>
      <span class="details-divider"></span>
      <div class="place">
        <svg width="17" height="24" viewBox="0 0 17 24"><path d="M8.5 0C3.8 0 0 3.7 0 8.3 0 14 8.5 24 8.5 24S17 14 17 8.3C17 3.7 13.2 0 8.5 0z" fill="#e8402a"/><circle cx="8.5" cy="8.3" r="3.3" fill="#fff"/></svg>
        El Pimiento,<br>Av. Julián Marcano 318
      </div>
    </div>
    <p class="blurb">Corvantel y Tidewell Labs le invitan a descubrir cómo reducir costos, aumentar la automatización y mejorar la satisfacción de los clientes a través de una solución única para enfrentar los desafíos de la banca</p>
    <div class="partners">
      <span class="partner"><span class="partner-dot"></span>Corvantel</span>
      <span class="partner">Tidewell Labs</span>
    </div>
    <a class="register" href="https://signup.corvantel-events.example/ledgerline-dinner"><span class="register-label">BOOK NOW</span><span class="register-url">https://signup.corvantel-events.example/ledgerline-dinner</span></a>
  </div>
</article>

<article class="invitation invitation--tasting">
  <div class="side-band side-band--left"></div>
  <div class="side-band side-band--right"></div>
  <div class="marble marble--top" role="img" aria-label="Textura de mármol dorado suave"></div>
  <div class="marble marble--bottom" role="img" aria-label="Textura de mármol dorado suave"></div>
  <div class="content">
    <p class="greeting">Estás invitado a la</p>
    <h1 class="event-title event-title--tasting">CATA DE<br>VINOS</h1>
    <p class="lead">PARA PRESENTAR EL SOFTWARE</p>
    <p class="product">HARBORVIEW OPERATIONS HUB</p>
    <div class="date"><span class="date-day">26<span class="date-de">de</span></span><span class="date-month">SEPTIEMBRE</span></div>
    <div class="details">
      <div class="time"><p class="time-label">TIME</p><p class="time-value">7 PM</p></div>
      <span class="details-divider"></span>
      <div class="place">
        <svg width="17" height="24" viewBox="0 0 17 24"><path d="M8.5 0C3.8 0 0 3.7 0 8.3 0 14 8.5 24 8.5 24S17 14 17 8.3C17 3.7 13.2 0 8.5 0z" fill="#e8402a"/><circle cx="8.5" cy="8.3" r="3.3" fill="#fff"/></svg>
        El Pimiento,<br>Av. Julián Marcano 318
      </div>
    </div>
    <p class="blurb">Corvantel y Tidewell Labs le invitan a conocer una solución que le permitirá a toda su empresa brindar una experiencia de servicio a otro nivel.</p>
    <div class="partners">
      <span class="partner"><span class="partner-dot"></span>Corvantel</span>
      <span class="partner">Tidewell Labs</span>
    </div>
    <a class="register" href="https://signup.corvantel-events.example/harborview-tasting"><span class="register-label">BOOK NOW</span><span class="register-url">https://signup.corvantel-events.example/harborview-tasting</span></a>
  </div>
</article>

</body>
</html>
```